Web Design For Manufacturing And Outsourcing Company

Pick up the pieces from our previous developer and help us complete our website.

5 pages - Home,Machining,Sourcing,About Us, and Contact

Attached you will find screen shots of previous direction but we're open to new ideas.

We can provide all text and images needed.

Thanks!

Number of Pages Required

5+ page

```html
<!DOCTYPE html>
<html lang="en">
<head>
<meta charset="utf-8">
<title>Ardent Industries</title>
<link rel="stylesheet" href="https://fonts.googleapis.com/css2?family=Montserrat:wght@300;400;600;700;800&family=PT+Sans:wght@400;700&display=swap">
<style>
:root{
  --orange:#e8471e;
  --ink:#2b2b2b;
  --white:#ffffff;
  --panel-left:#f3f0f0;
  --panel-right:#ededec;
  --band:#f1efef;
  --footer:#1d1d1e;
  --footer-text:#d6d6d6;
  --rule:#cfcfcf;
}
*{box-sizing:border-box;margin:0;padding:0}
html,body{width:1200px;height:2517px;overflow:hidden}
body{position:relative;font-family:"PT Sans",Arial,sans-serif;color:var(--ink);background:var(--white)}
.abs{position:absolute}
.btn{position:absolute;background:var(--orange);color:var(--white);font-family:"Montserrat",Arial,sans-serif;font-weight:700;font-size:14px;letter-spacing:.3px;display:flex;align-items:center;justify-content:center;text-decoration:none}

/* hero */
.hero{position:absolute;left:0;top:0;width:1200px;height:653px;background:radial-gradient(circle at 660px 510px,#cfe4ff 0,#6f8fb8 25px,#8a4a25 90px,#3a2a22 260px,#161616 620px)}
.brand{position:absolute;display:flex;align-items:center;gap:10px;font-family:"Montserrat",Arial,sans-serif;font-weight:700;letter-spacing:3px;color:var(--orange)}
.brand .mark{background:var(--orange);display:block}
.hero .brand{left:30px;top:36px;font-size:18px}
.hero .brand .mark{width:22px;height:22px}
.nav{position:absolute;top:32px;right:40px;display:flex;gap:32px;font-family:"Montserrat",Arial,sans-serif;font-weight:700;font-size:13px;color:var(--white)}
.nav a{color:inherit;text-decoration:none;padding-bottom:8px}
.nav a.active{color:var(--orange);border-bottom:2px solid var(--orange)}
.hero h1{position:absolute;left:82px;top:300px;width:470px;font-family:"Montserrat",Arial,sans-serif;font-weight:800;font-size:33px;line-height:38px;color:var(--white)}
.dots{position:absolute;left:548px;top:601px;display:flex;gap:12px}
.dots i{width:11px;height:11px;border-radius:50%;background:var(--white);display:block}
.dots i.on{background:var(--orange);border:2px solid var(--white)}

/* services */
.service{position:absolute;top:653px;width:598px;height:534px;text-align:center}
.service.machining{left:0;background:var(--panel-left)}
.service.sourcing{left:603px;width:597px;background:var(--panel-right)}
.service .dash{position:absolute;left:50%;top:64px;width:42px;height:4px;margin-left:-21px;background:#a9a9a9}
.service h2{position:absolute;left:0;right:0;top:86px;font-family:"Montserrat",Arial,sans-serif;font-weight:800;font-size:24px}
.service p{position:absolute;left:160px;right:160px;top:140px;font-size:16px;line-height:21px}
.service .btn{left:234px;top:260px;width:130px;height:37px}
.service .art{position:absolute;left:60px;right:20px;top:355px;height:172px}
.machining .art{background:linear-gradient(180deg,var(--panel-left) 0,#e9e3e5 40%,#f5d6cc 100%)}
.sourcing .art{background:linear-gradient(180deg,var(--panel-right) 0,#f3dcd3 50%,#f7c6b6 100%)}
.service .base{position:absolute;left:0;right:0;bottom:0;height:5px}
.machining .base{background:#1e1e1e}
.sourcing .base{background:var(--orange)}

/* welcome */
.welcome-photo{position:absolute;left:143px;top:1267px;width:405px;height:511px;background:linear-gradient(160deg,#c9d9ea 0,#5f7fa8 45%,#1c3563 100%)}
.welcome .kicker{position:absolute;left:618px;top:1276px;font-family:"Montserrat",Arial,sans-serif;font-weight:400;font-size:20px}
.welcome h2{position:absolute;left:618px;top:1300px;font-family:"Montserrat",Arial,sans-serif;font-weight:800;font-size:35px;color:var(--orange)}
.welcome p{position:absolute;left:618px;top:1366px;width:415px;font-size:15.5px;line-height:21px}
.values{position:absolute;left:618px;top:1578px;width:430px;display:flex}
.value{width:160px;text-align:center;font-family:"Montserrat",Arial,sans-serif;font-size:12.5px;font-weight:600;border-right:1px solid var(--rule)}
.value:last-child{border-right:none}
.value svg{display:block;margin:0 auto 14px}
.value:first-child{width:100px;margin-left:-18px}
.welcome .btn{left:623px;top:1724px;width:132px;height:38px}

/* call to action */
.cta{position:absolute;left:0;top:1862px;width:1200px;height:286px;background:var(--band);text-align:center;font-family:"Montserrat",Arial,sans-serif}
.cta .l1{position:absolute;left:0;right:0;top:68px;font-weight:300;font-size:28px}
.cta .l2{position:absolute;left:0;right:0;top:110px;font-weight:800;font-size:29px}
.cta .btn{left:508px;top:223px;width:185px;height:41px;font-size:16px}

/* footer */
.footer{position:absolute;left:0;top:2148px;width:1200px;height:369px;background:var(--footer);color:var(--footer-text);font-size:12px}
.footer .brand{left:145px;top:110px;font-size:19px}
.footer .brand .mark{width:24px;height:24px}
.fcol{position:absolute;top:54px}
.fcol h3{font-family:"Montserrat",Arial,sans-serif;font-weight:700;font-size:12.5px;color:var(--white);margin-bottom:18px}
.fcol.contact{left:450px}
.fcol.menu{left:732px}
.fcol.social{left:944px}
.citem{display:flex;gap:12px;margin-bottom:18px;line-height:17px}
.citem svg{flex:none;margin-top:2px}
.menu li{list-style:none;line-height:18px}
.sitem{display:flex;align-items:center;gap:12px;margin-bottom:14px}
.sitem i{width:26px;height:26px;border-radius:50%;display:block}
.footer .rule{position:absolute;left:112px;right:150px;top:269px;height:1px;background:#3a3a3a}
.footer .copy{position:absolute;left:0;right:0;top:312px;text-align:center;font-size:11.5px}
</style>
</head>
<body>

<header class="hero" role="img" aria-label="Close-up photograph of a laser cutting head throwing orange sparks onto sheet metal">
  <div class="brand"><span class="mark"></span>ARDENT INDUSTRIES</div>
  <nav class="nav">
    <a class="active">HOME</a><a>MACHINING CAPABILITIES</a><a>SOURCING</a><a>CONTACT US</a>
  </nav>
  <h1>A SINGLE POINT OF CONTACT FOR ALL YOUR PROCUREMENT NEEDS.</h1>
  <div class="dots"><i></i><i></i><i class="on"></i><i></i><i></i></div>
</header>

<section class="service machining">
  <span class="dash"></span>
  <h2>MACHINING</h2>
  <p>Whether Prototype, quick turn, short or medium run production, our in house capabilities can help you with any maching needs you may have.</p>
  <a class="btn">READ MORE</a>
  <div class="art" role="img" aria-label="Illustration of a robotic arm, conveyor belt with boxes, gears and a forklift"></div>
  <span class="base"></span>
</section>

<section class="service sourcing">
  <span class="dash"></span>
  <h2>SOURCING</h2>
  <p>We offer a One Stop Shop solution be leveraging existing relationships and supply base knowledge to source hard to locate items, components and assemblies at the lowest cost</p>
  <a class="btn">READ MORE</a>
  <div class="art" role="img" aria-label="Illustration of a delivery truck, trees and workers moving parcels on hand trucks"></div>
  <span class="base"></span>
</section>

<section class="welcome">
  <div class="welcome-photo" role="img" aria-label="Photograph of two business people shaking hands over a blue city skyline"></div>
  <div class="kicker">WELCOME TO</div>
  <h2>ARDENT INDUSTRIES</h2>
  <p>We are committed to consistently exceeding customer expectations by providing products, services and sourcing solutions of the highest standard of quality. With our streamlined processes our method is efficient, provides value and ensures on time delivery. Our success is based on continuously improving the efficiencies and effectiveness of our products, processes, and quality management systems.</p>
  <div class="values">
    <div class="value">
      <svg width="62" height="62" viewBox="0 0 62 62"><circle cx="31" cy="31" r="31" fill="#d4d4d4"/><circle cx="25" cy="24" r="7" fill="#4a4a4a"/><circle cx="37" cy="24" r="7" fill="#4a4a4a"/><path d="M13 44c0-9 6-13 12-13s12 4 12 13zM27 44c0-9 5-13 10-13s12 4 12 13z" fill="#4a4a4a"/></svg>
      TEAMWORK
    </div>
    <div class="value">
      <svg width="62" height="62" viewBox="0 0 62 62"><circle cx="31" cy="31" r="31" fill="#d4d4d4"/><path d="M12 26l8-4 8 4 6-4 6 0 10 4v10l-8 6-6-4-6 4-8-6-10-4z" fill="#4a4a4a"/></svg>
      RESPECT
    </div>
    <div class="value">
      <svg width="62" height="62" viewBox="0 0 62 62"><circle cx="31" cy="31" r="31" fill="#d4d4d4"/><circle cx="35" cy="26" r="8" fill="none" stroke="#4a4a4a" stroke-width="5"/><circle cx="24" cy="38" r="6" fill="none" stroke="#4a4a4a" stroke-width="4"/></svg>
      GRATITUDE
    </div>
  </div>
  <a class="btn">READ MORE</a>
</section>

<section class="cta">
  <div class="l1">CONTACT US TODAY WITH YOUR</div>
  <div class="l2">MACHINING OR SOURCING NEEDS!</div>
  <a class="btn">GET IN TOUCH</a>
</section>

<footer class="footer">
  <div class="brand"><span class="mark"></span>ARDENT INDUSTRIES</div>
  <div class="fcol contact">
    <h3>CONTACT US</h3>
    <div class="citem"><svg width="9" height="12" viewBox="0 0 9 12"><path d="M4.5 0a4.5 4.5 0 0 0-4.5 4.5C0 8 4.5 12 4.5 12S9 8 9 4.5A4.5 4.5 0 0 0 4.5 0zm0 6.3a1.8 1.8 0 1 1 0-3.6 1.8 1.8 0 0 1 0 3.6z" fill="#d6d6d6"/></svg><span>Veldstraat 18<br>3811 PL &nbsp;Eemstad, The Netherlands</span></div>
    <div class="citem"><svg width="10" height="10" viewBox="0 0 10 10"><path d="M2 0l2 2.5-1 1.2a6 6 0 0 0 3.3 3.3l1.2-1L10 8l-1.5 2C4 10 0 6 0 1.5z" fill="#d6d6d6"/></svg><span>555.014.2230</span></div>
    <div class="citem"><svg width="11" height="9" viewBox="0 0 11 9"><rect width="11" height="9" fill="#d6d6d6"/><path d="M0 0l5.5 5L11 0" fill="none" stroke="#1d1d1e" stroke-width="1.2"/></svg><span>info@ardentindustries.com</span></div>
  </div>
  <div class="fcol menu">
    <h3>MENU</h3>
    <ul><li>HOME</li><li>MACHINING CAPABILITIES</li><li>SOURCING</li><li>CONTACT US</li></ul>
  </div>
  <div class="fcol social">
    <h3>CONNECT WITH US</h3>
    <div class="sitem"><i style="background:#3b5b9c"></i>Circlepage</div>
    <div class="sitem"><i style="background:#2aa3df"></i>Chirpline</div>
    <div class="sitem"><i style="background:#1b2a55"></i>Workgraph</div>
  </div>
  <span class="rule"></span>
  <div class="copy">Copyrights @ 2019 All Rights Reserved</div>
</footer>

</body>
</html>
```